Building company buisness cards

We are looking for a sharp modern new look for our business cards.
We are a New Zealand based company that specialises in house and land packages.
We have attached a photo of the current logo and would like to see if it can be improved somehow if needed.
We are open to any colours but we have chosen green at this stage.
Feel free to change the font and make the logo smarter looking.
Play with the colours and see what looks best.

We want a card that looks so good know one will want to throw it away!

Target Market(s)

Home buyers

Industry/Entity Type

Building

Contact Information for Business Card

Derek Tolvane
0217394062
dtolvane@quillmarkhomesteads.co.nz
quillmarkhomesteads.co.nz

Font styles to use
Serif
Sans Serif

Colors

Designer to choose colors to be used in the design.

Requirements
Must have
• Logo and company name on one side, details on the other side
Nice to have
• Color codes for the original green are HEX #4a8028, RGB(74,128,40), CMYK(42,0,69,50)
• Round corners, Raised and/or spot UV

```html
<!DOCTYPE html>
<html lang="en">
<head>
<meta charset="utf-8">
<title>Quillmark Homesteads — Business Card</title>
<link rel="stylesheet" href="https://fonts.googleapis.com/css2?family=Lato:wght@400;700;900&display=swap">
<style>
  :root {
    --backdrop: #9a9a9a;
    --brand-green: #4a8028;
    --card-white: #ffffff;
    --ink: #3a3a3a;
    --rule-light: #c9d9bd;
    --rule-on-green: #7fae5c;
  }
  * { margin: 0; padding: 0; box-sizing: border-box; }
  html, body { width: 1200px; height: 900px; overflow: hidden; }
  body {
    background: var(--backdrop);
    font-family: "Lato", Arial, sans-serif;
    position: relative;
  }
  .card {
    position: absolute;
    width: 478px;
    height: 294px;
    box-shadow: 3px 3px 4px rgba(0,0,0,0.35);
  }
  .card--details {
    left: 120px; top: 275px;
    background: var(--card-white);
    border-radius: 0 46px 0 46px;
  }
  .card--brand {
    left: 607px; top: 274px;
    background: var(--brand-green);
    border-radius: 46px 0 46px 0;
  }
  .wordmark {
    position: absolute;
    text-align: center;
    font-weight: 900;
    letter-spacing: -0.3px;
    line-height: 1.05;
  }
  .card--details .wordmark {
    left: 200px; width: 250px; top: 98px;
    color: var(--brand-green);
    font-size: 25px;
  }
  .card--brand .wordmark {
    left: 0; width: 478px; top: 138px;
    color: var(--card-white);
    font-size: 34px;
  }
  .wordmark__rule {
    position: absolute;
    height: 1px;
  }
  .card--details .wordmark__rule { left: 301px; width: 51px; top: 168px; background: var(--rule-light); }
  .card--brand .wordmark__rule { left: 205px; width: 68px; top: 220px; background: var(--rule-on-green); }
  .holder-name {
    position: absolute;
    left: 37px; top: 175px;
    color: var(--brand-green);
    font-size: 17px;
    font-weight: 700;
    text-transform: uppercase;
    letter-spacing: 0.2px;
  }
  .contact-list {
    position: absolute;
    left: 36px; top: 209px;
    list-style: none;
    color: var(--ink);
    font-size: 13.5px;
    line-height: 17px;
  }
  .contact-list li { display: flex; align-items: center; gap: 5px; }
  .contact-list svg { width: 11px; height: 11px; fill: var(--brand-green); flex: none; }
</style>
</head>
<body>
  <section class="card card--details">
    <div class="wordmark">quillmark<br>homesteads.</div>
    <div class="wordmark__rule"></div>
    <h1 class="holder-name">Derek Tolvane</h1>
    <ul class="contact-list">
      <li>
        <svg viewBox="0 0 12 12" aria-hidden="true"><path d="M1 4c0-2 2-3 5-3s5 1 5 3v1H8.5V3.8C8 3.3 7 3 6 3s-2 .3-2.5.8V5H1zM3 6h6l2 5H1zM6 7.2a1.3 1.3 0 100 2.6 1.3 1.3 0 000-2.6z"/></svg>
        0217394062
      </li>
      <li>
        <svg viewBox="0 0 12 12" aria-hidden="true"><path d="M1 2.5h10v7H1zM1.6 3l4.4 3.6L10.4 3v1L6 7.6 1.6 4z" fill-rule="evenodd"/></svg>
        dtolvane@quillmarkhomesteads.co.nz
      </li>
      <li>
        <svg viewBox="0 0 12 12" aria-hidden="true"><circle cx="6" cy="6" r="5"/><path d="M3 4.5c1 0 1.5 1 2.5 1s.5 1.5 0 2-1 1-1 2M8 2.5c-.5 1 .5 1.5 1.5 1.5M8.5 7c-.5.5-1 1.5-.5 2" stroke="#fff" stroke-width="0.9" fill="none"/></svg>
        www.quillmarkhomesteads.co.nz
      </li>
    </ul>
  </section>

  <section class="card card--brand">
    <div class="wordmark">quillmark<br>homesteads.</div>
    <div class="wordmark__rule"></div>
  </section>
</body>
</html>
```